Business Cards Needed for Innovative Healthcare Marketing Company

We are a marketing company focused on healthcare. Our company is all about rebranding yourself renewing your image and generating results. The phoenix stands for "reborn" or "rising" which we provide new brands for our clients we take their old brands and renew it with creativity and innovation. I am looking for a business card with color dimension. I have attached an example of a card I think has the look and feel of what I am trying to accomplish. I like that the card example has black and grey font colors, I like the font placement and the small logo, I really like the use of the colors on the right those are the colors of my logo. My logo is phoenix so maybe incorporating flames similar to that design. I would like the back a solid color maybe red with an opaque version of the logo and website. As a marketing company I am always open to creative liberty!

Target Market(s)

Doctors and business professionals.

Industry/Entity Type

Marketing

Contact Information for Business Card

Valcorne Health Care Marketing
Marla Tenwick- CEO
#(512)638-2974
email-marla@valcorne.com
website- valcorne.com

Font styles to use
Sans Serif

Colors
ec1f27
f37122
ffc214
fbed22
fbf289
f04a50

Requirements
Must have
• The logo and required information
Nice to have
• icons by the information
Should not have
• child like font

```html
<!DOCTYPE html>
<html lang="en">
<head>
<meta charset="utf-8">
<title>Valcorne Health Care Marketing – Business Card</title>
<link href="https://fonts.googleapis.com/css2?family=Open+Sans:wght@300;400;700&display=swap" rel="stylesheet">
<style>
  :root{
    --red:#ec1f27;
    --red-soft:#f04a50;
    --yellow:#fbed22;
    --yellow-pale:#fbf289;
    --orange:#f37122;
    --gold:#ffc214;
    --paper:#ffffff;
    --ink:#555555;
    --backdrop:#e6e3de;
  }
  html,body{margin:0;padding:0;overflow:hidden;}
  body{width:1200px;height:1023px;background:var(--backdrop);font-family:"Open Sans",sans-serif;position:relative;}
  .card{position:absolute;left:250px;width:700px;height:400px;background:var(--paper);border-radius:22px;overflow:hidden;box-shadow:0 6px 18px rgba(0,0,0,.18);}
  .card--front{top:60px;}
  .card--back{top:563px;}
  .card__art{position:absolute;inset:0;}
  .brand{position:absolute;display:flex;align-items:center;gap:14px;color:var(--red);font-weight:300;text-transform:uppercase;white-space:nowrap;}
  .brand__dot{width:38px;height:38px;border-radius:50%;background:var(--orange);flex:none;}
  .card--front .brand{left:48px;top:100px;font-size:17px;letter-spacing:.04em;}
  .card--back .brand{left:0;right:0;top:110px;justify-content:center;font-size:28px;letter-spacing:.06em;}
  .card--back .brand__dot{width:52px;height:52px;}
  .person{position:absolute;left:100px;top:170px;}
  .person__name{margin:0;color:var(--red);font-weight:700;font-size:26px;}
  .person__title{margin:0;color:var(--orange);font-size:14px;}
  .contact{position:absolute;left:100px;top:250px;list-style:none;margin:0;padding:0;}
  .contact__item{display:flex;align-items:center;gap:12px;color:var(--ink);font-size:15px;margin-bottom:11px;}
  .contact__icon{width:22px;height:22px;flex:none;}
</style>
</head>
<body>

<section class="card card--front">
  <svg class="card__art" viewBox="0 0 700 400" aria-hidden="true">
    <path d="M0 0 H430 C380 50 250 75 0 72 Z" fill="var(--yellow-pale)"/>
    <path d="M0 0 H410 C360 40 240 60 0 58 Z" fill="var(--yellow)"/>
    <path d="M560 0 C470 90 460 260 555 400 H700 V0 Z" fill="var(--red-soft)" opacity=".7"/>
    <path d="M590 0 C510 90 505 270 590 400 H700 V0 Z" fill="var(--red)"/>
  </svg>

  <div class="brand"><span class="brand__dot"></span>Valcorne Health Care Marketing</div>

  <div class="person">
    <p class="person__name">Marla Tenwick</p>
    <p class="person__title">Title</p>
  </div>

  <ul class="contact">
    <li class="contact__item">
      <svg class="contact__icon" viewBox="0 0 22 22" aria-hidden="true"><rect width="22" height="22" rx="4" fill="var(--red)"/><path d="M7 5 L9.5 8 8.5 9.5 C9.5 11.5 10.5 12.5 12.5 13.5 L14 12.5 17 15 15.5 17 C10 16.5 5.5 12 5 6.5 Z" fill="#fff"/></svg>
      (512)638-2974
    </li>
    <li class="contact__item">
      <svg class="contact__icon" viewBox="0 0 22 22" aria-hidden="true"><rect width="22" height="22" rx="4" fill="var(--red)"/><rect x="5" y="7" width="12" height="8" fill="none" stroke="#fff" stroke-width="1.5"/><path d="M5 7 L11 12 17 7" fill="none" stroke="#fff" stroke-width="1.5"/></svg>
      marla@valcorne.com
    </li>
    <li class="contact__item">
      <svg class="contact__icon" viewBox="0 0 22 22" aria-hidden="true"><circle cx="11" cy="11" r="9" fill="none" stroke="var(--red)" stroke-width="1.6"/><ellipse cx="11" cy="11" rx="4" ry="9" fill="none" stroke="var(--red)" stroke-width="1.3"/><path d="M2 11 H20 M4 6.5 H18 M4 15.5 H18" stroke="var(--red)" stroke-width="1.3"/></svg>
      www.valcorne.com
    </li>
  </ul>
</section>

<section class="card card--back">
  <svg class="card__art" viewBox="0 0 700 400" aria-hidden="true">
    <path d="M0 260 C200 240 380 260 520 400 H0 Z" fill="var(--red-soft)" opacity=".7"/>
    <path d="M0 275 C210 258 370 290 490 400 H0 Z" fill="var(--red)"/>
    <path d="M700 200 C620 220 540 300 500 400 H700 Z" fill="var(--yellow-pale)"/>
    <path d="M700 225 C640 250 585 320 560 400 H700 Z" fill="var(--yellow)"/>
  </svg>

  <div class="brand"><span class="brand__dot"></span>Valcorne Health Care Marketing</div>
</section>

</body>
</html>
```